BRKA Tennis Donor Informational Packet

We need a powerpoint presentation designed in 8.5x11 format that it can be easily printed out and handed out to potential donors. We are a nonprofit tennis center in Maryland that aims to provide access to "Rackets for Anyone". The design should be bright and clean, clearly highlighting key facts and emphasizing photos, utilizing the BRKA blue and green.

The project should follow the progression of the Velm project guidelines and use the other files as resources to find updated information/color photos.

Industry/Entity Type

Nonprofit Tennis Center, Sports

Font styles to use
Sans Serif

Colors
0054AA
0677BA
7BADD7
CADEEF
E8F1F8
59FF00
82FF00
B8FF75
E3FFCB
F4FFEA

Requirements
Must have
• BRKA Blue and Green, use of information and photos provided
Nice to have
• use of tennis graphics, tennis elements
Should not have
• Typos, information left out

```html
<!DOCTYPE html>
<html lang="en">
<head>
<meta charset="utf-8">
<title>BRKA Donor Packet Slides</title>
<link href="https://fonts.googleapis.com/css2?family=Roboto:ital,wght@0,400;0,700;1,400&family=Roboto+Slab:wght@400;700&display=swap" rel="stylesheet">
<style>
:root{
  --blue:#1b4fa3;
  --blue-deep:#163f86;
  --green:#9dbf4f;
  --green-dark:#6f9a2c;
  --white:#ffffff;
  --ink:#1a1a1a;
  --page:#ffffff;
}
*{margin:0;padding:0;box-sizing:border-box}
html,body{width:1200px;height:1200px;overflow:hidden;background:var(--page)}
body{position:relative;font-family:"Roboto Slab",serif;color:var(--ink)}
.slide{position:absolute;width:472px;height:365px;background:var(--white);overflow:hidden;box-shadow:0 1px 4px rgba(0,0,0,.35)}
.slide > svg.frame{position:absolute;left:0;top:0;width:472px;height:365px}
.s1{left:120px;top:44px}
.s2{left:625px;top:46px}
.s3{left:120px;top:426px}
.s4{left:622px;top:423px}
.s5{left:114px;top:811px}
.brand{position:absolute;left:0;right:0;text-align:center;font-family:"Roboto",sans-serif;font-weight:700;color:var(--blue);letter-spacing:1px;display:flex;justify-content:center;align-items:center;gap:7px}
.brand .dot{display:inline-block;border-radius:50%;background:var(--blue)}
.brand-lg{top:8px;font-size:42px}
.brand-lg .dot{width:22px;height:22px}
.brand-md{top:6px;font-size:30px}
.brand-md .dot{width:16px;height:16px}
.brand-sm{top:8px;font-size:24px}
.brand-sm .dot{width:13px;height:13px}
.tagline{position:absolute;top:50px;left:0;right:0;text-align:center;font-family:"Roboto",sans-serif;font-weight:700;font-size:8px;letter-spacing:2px;color:var(--blue);padding-left:18px}
.photo{position:absolute}
.cover-title{position:absolute;left:9px;top:314px;font-family:"Roboto Slab",serif;font-weight:700;font-size:31px;color:var(--green-dark)}
.bullets{position:absolute;list-style:none;font-size:13px;line-height:19.6px}
.bullets li{position:relative;padding-left:16px}
.bullets li::before{content:"";position:absolute;left:0;top:6px;width:8px;height:8px;border-radius:50%;background:var(--ink)}
.s2 .bullets{left:40px;top:90px;width:420px}
.s2 .bullets li{margin-bottom:19px}
.s2 .bullets li:first-child{margin-bottom:0}
.s3 .bullets{left:200px;top:72px;width:262px;text-align:justify}
.contact{position:absolute;bottom:10px;left:18px;right:0;display:flex;font-family:"Roboto Slab",serif;font-weight:700;font-size:12px;color:var(--white)}
.contact span{display:flex;align-items:center;gap:6px}
.contact .email{width:200px}
.contact svg{width:12px;height:12px;fill:var(--white)}
.quote{position:absolute;left:295px;top:80px;width:165px;font-family:"Roboto",sans-serif;font-style:italic;font-size:12px;line-height:15.5px;text-align:justify;color:var(--ink)}
.section-title{position:absolute;top:57px;left:140px;width:320px;text-align:center;font-weight:700;font-size:12px;color:var(--blue)}
.path-label{position:absolute;left:18px;top:100px;width:60px;height:183px;display:flex;align-items:center;justify-content:center}
.path-label p{transform:rotate(-90deg);white-space:nowrap;font-weight:700;font-size:12.5px;line-height:14px;color:var(--white);text-align:left}
.pillar{position:absolute;left:140px;width:320px;height:72px;background:var(--green);color:var(--white);padding:8px 3px 0 82px}
.pillar h3{font-size:12px;font-weight:700;text-align:center;margin-bottom:2px}
.pillar p{font-size:7.4px;line-height:12px;text-align:justify}
.p1{top:77px}.p2{top:161px}.p3{top:243px}
.pillar-icon{position:absolute;width:76px;height:76px}
</style>
</head>
<body>

<!-- Cover -->
<section class="slide s1">
  <svg class="frame" viewBox="0 0 472 365">
    <polygon points="0,0 160,0 0,105" fill="var(--blue)"/>
    <polygon points="472,0 472,90 440,0" fill="var(--blue)"/>
    <polygon points="472,230 472,365 360,365" fill="var(--blue)"/>
  </svg>
  <div class="brand brand-lg"><span class="dot"></span>BRKA</div>
  <div class="tagline">RACKETS FOR ANYONE</div>
  <div class="photo" role="img" aria-label="Group photo of young players in blue club shirts holding rackets on a court" style="left:0;top:72px;width:472px;height:240px;background:linear-gradient(180deg,#4f7a4a 0%,#3a6fc4 35%,#2f66c0 70%,#8a8f93 100%)"></div>
  <h1 class="cover-title">Rackets for Anyone</h1>
</section>

<!-- Bullet slide -->
<section class="slide s2">
  <svg class="frame" viewBox="0 0 472 365">
    <rect x="0" y="0" width="472" height="70" fill="var(--green)"/>
    <polygon points="0,0 160,0 0,128" fill="var(--blue)"/>
    <polygon points="430,0 472,0 472,70" fill="var(--blue)"/>
    <rect x="0" y="325" width="472" height="40" fill="var(--green)"/>
    <polygon points="472,268 472,365 360,365" fill="var(--blue)"/>
  </svg>
  <div class="brand brand-md"><span class="dot"></span>BRKA</div>
  <ul class="bullets">
    <li>Lorem Ipsum is simply dummy text of the printing and typesetting industry.</li>
    <li>There are many variations of passages of Lorem Ipsum available, but the majority have suffered alteration in some form,</li>
    <li>The standard chunk of Lorem Ipsum used since the 1500s is reproduced below for those interested</li>
    <li>On the other hand, we denounce with righteous indignation and dislike men who are so beguiled and demoralized by the charms of pleasure of the moment</li>
  </ul>
  <div class="contact">
    <span class="email"><svg viewBox="0 0 12 12"><rect x="0" y="2" width="12" height="8"/></svg>Email : info@brka.org</span>
    <span><svg viewBox="0 0 12 12"><path d="M2 0h3l1 3-2 1q1 3 4 4l1-2 3 1v3q-1 2-3 1Q2 9 0 3 0 0 2 0z"/></svg>Phone :(555)-014-2200</span>
  </div>
</section>

<!-- Photo + text slide -->
<section class="slide s3">
  <svg class="frame" viewBox="0 0 472 365">
    <rect x="0" y="0" width="472" height="50" fill="var(--green)"/>
    <polygon points="0,0 80,0 0,55" fill="var(--blue)"/>
    <rect x="0" y="335" width="472" height="30" fill="var(--green)"/>
    <polygon points="472,300 472,365 390,365" fill="var(--blue)"/>
  </svg>
  <div class="brand brand-sm"><span class="dot"></span>BRKA</div>
  <div class="photo" role="img" aria-label="Young player holding a trophy after a tournament win" style="left:8px;top:75px;width:188px;height:195px;border-radius:12px;background:radial-gradient(circle at 55% 50%,#c9a27e 0%,#e9e9e9 40%,#2c4f99 80%)"></div>
  <ul class="bullets">
    <li>At vero eos et accusamus et iusto odio dignissimos ducimus qui blanditiis praesentium voluptatum deleniti atque corrupti quos dolores et quas molestias excepturi sint occaecati cupiditate non provident, similique sunt in culpa qui officia deserunt mollitia animilaborum et dolorum fuga. Et harum quidem rerum facilis est et expedita distinctio. Nam libero tempore.who are so beguiled and demoralized by the charms of pleasure of the moment</li>
  </ul>
  <div class="contact">
    <span class="email"><svg viewBox="0 0 12 12"><rect x="0" y="2" width="12" height="8"/></svg>Email : info@brka.org</span>
    <span><svg viewBox="0 0 12 12"><path d="M2 0h3l1 3-2 1q1 3 4 4l1-2 3 1v3q-1 2-3 1Q2 9 0 3 0 0 2 0z"/></svg>Phone : (555)-014-2200</span>
  </div>
</section>

<!-- Full photo slide -->
<section class="slide s4">
  <div class="photo" role="img" aria-label="Young child swinging a racket at a ball on a hard court" style="left:0;top:45px;width:472px;height:290px;background:linear-gradient(180deg,#3d5a34 0%,#6b7a5a 35%,#8d98aa 55%,#7f8ea6 100%)"></div>
  <svg class="frame" viewBox="0 0 472 365">
    <rect x="0" y="0" width="472" height="48" fill="var(--green)"/>
    <polygon points="0,0 75,0 0,55" fill="var(--blue)"/>
    <rect x="0" y="332" width="472" height="33" fill="var(--green)"/>
    <polygon points="472,300 472,365 390,365" fill="var(--blue)"/>
    <polygon points="240,92 275,72 472,62 472,140 290,150 240,125" fill="var(--white)"/>
  </svg>
  <div class="brand brand-sm" style="top:6px"><span class="dot"></span>BRKA</div>
  <p class="quote">Lorem Ipsum is simply dummy text of the printing and typesetting industry.</p>
  <div class="contact">
    <span class="email"><svg viewBox="0 0 12 12"><rect x="0" y="2" width="12" height="8"/></svg>Email : info@brka.org</span>
    <span><svg viewBox="0 0 12 12"><path d="M2 0h3l1 3-2 1q1 3 4 4l1-2 3 1v3q-1 2-3 1Q2 9 0 3 0 0 2 0z"/></svg>Phone : (555)-014-2200</span>
  </div>
</section>

<!-- Commitment slide -->
<section class="slide s5">
  <svg class="frame" viewBox="0 0 472 365">
    <rect x="0" y="0" width="472" height="48" fill="var(--green)"/>
    <polygon points="0,0 75,0 0,55" fill="var(--blue)"/>
    <rect x="0" y="335" width="472" height="30" fill="var(--green)"/>
    <polygon points="472,300 472,365 390,365" fill="var(--blue)"/>
    <polygon points="18,100 70,100 100,187 70,283 18,283" fill="var(--blue)"/>
    <g stroke="var(--blue)" stroke-width="1.2" fill="none">
      <line x1="100" y1="187" x2="138" y2="125"/>
      <line x1="100" y1="187" x2="138" y2="197"/>
      <line x1="100" y1="187" x2="138" y2="268"/>
    </g>
    <circle cx="100" cy="187" r="10" fill="#d8d8d8" stroke="#aaa"/>
  </svg>
  <div class="brand brand-sm"><span class="dot"></span>BRKA</div>
  <h2 class="section-title">Our Commitment</h2>
  <div class="path-label"><p>THE PATHWAY TO<br>EXCELLENCE</p></div>

  <div class="pillar p1"><h3>Introduction To Tennis</h3><p>Lorem Ipsum is simply dummy text of the printing and typesetting industry. Lorem Ipsum has been the industry's standard dummy text ever since the 1500s.</p></div>
  <div class="pillar p2"><h3>Talent Development</h3><p>There are many variations of passages of Lorem Ipsum available, but the majority have suffered alteration in some form, by injected humour</p></div>
  <div class="pillar p3"><h3>Achieving Excellence</h3><p>The standard chunk of Lorem Ipsum used since the 1500s is reproduced below for those interested. Sections 1.10.32 and 1.10.33 from "de Finibus Bonorum et Malorum" by Tullus are also reproduced in their exact original form,</p></div>

  <svg class="pillar-icon" style="left:134px;top:75px" viewBox="0 0 76 76">
    <circle cx="38" cy="38" r="36" fill="#ececec" stroke="var(--green)" stroke-width="2"/>
    <ellipse cx="44" cy="30" rx="13" ry="10" transform="rotate(-40 44 30)" fill="none" stroke="var(--green)" stroke-width="3"/>
    <line x1="35" y1="40" x2="20" y2="56" stroke="var(--green)" stroke-width="4" stroke-linecap="round"/>
    <circle cx="24" cy="26" r="4" fill="var(--green)"/>
  </svg>
  <svg class="pillar-icon" style="left:134px;top:159px" viewBox="0 0 76 76">
    <circle cx="38" cy="38" r="36" fill="#ececec" stroke="var(--green)" stroke-width="2"/>
    <g fill="var(--green)"><rect x="18" y="44" width="7" height="12"/><rect x="28" y="38" width="7" height="18"/><rect x="38" y="32" width="7" height="24"/><rect x="48" y="24" width="7" height="32"/><polygon points="51.5,14 57,22 46,22"/></g>
  </svg>
  <svg class="pillar-icon" style="left:134px;top:241px" viewBox="0 0 76 76">
    <circle cx="38" cy="38" r="36" fill="#ececec" stroke="var(--green)" stroke-width="2"/>
    <polygon points="40,12 43,21 52,21 45,26 48,35 40,29 32,35 35,26 28,21 37,21" fill="var(--green)"/>
    <g fill="var(--green)"><rect x="22" y="42" width="7" height="16"/><path d="M31 42h6l3-8h4v8h8v14H31z"/></g>
  </svg>

  <div class="contact">
    <span class="email"><svg viewBox="0 0 12 12"><rect x="0" y="2" width="12" height="8"/></svg>Email : info@brka.org</span>
    <span><svg viewBox="0 0 12 12"><path d="M2 0h3l1 3-2 1q1 3 4 4l1-2 3 1v3q-1 2-3 1Q2 9 0 3 0 0 2 0z"/></svg>Phone : (555)-014-2200</span>
  </div>
</section>

</body>
</html>
```